van wrap for house/commercial painting company

We are rebranding and i need a new design for a los angeles based painting company.  New business name will be Orla Painting and the vehicle is a bex cargolux 2300.
We offer our services to houses, hoa's, commercial and specializing in interior/exterior, wood staining, cabinet refinishing, drywall repair.
We would love a colorful but easy to read design to grab attention when at job sites or on the road.
I attached our current wrap which we no longer like and looking for a different look/feel. I attached our current logo but the color splash is not necessary if  design flows better without it.

house painting
- easy to read phone number and contact info

```html
<!DOCTYPE html>
<html lang="en">
<head>
<meta charset="utf-8">
<title>Orla Painting – Bex Cargolux 2300 Wrap</title>
<link href="https://fonts.googleapis.com/css2?family=Montserrat:wght@500;600;800&display=swap" rel="stylesheet">
<style>
  :root{
    --bg:#1b1b1c;
    --blue:#2f86d4;
    --red:#e2202b;
    --red-deep:#c4141f;
    --orange:#f58a1f;
    --yellow:#f9c12e;
    --white:#ffffff;
    --ink:#3b3b3d;
    --rule:#2d2d2f;
  }
  *{margin:0;padding:0;box-sizing:border-box}
  html,body{width:1200px;height:1200px;overflow:hidden;background:var(--bg)}
  body{position:relative;font-family:"Montserrat",sans-serif}
  .panel{position:absolute;overflow:hidden;border-radius:14px}
  .panel svg{position:absolute;inset:0;width:100%;height:100%}
  .abs{position:absolute;white-space:nowrap}

  .brand-name{font-weight:800;color:var(--ink);line-height:1;letter-spacing:2px}
  .brand-sub{font-weight:600;color:var(--ink);line-height:1}
  .phone{font-weight:800;color:var(--white);line-height:1}
  .services{list-style:none;color:var(--white);font-weight:800;text-transform:uppercase}
  .services li::before{content:"•";margin-right:10px}
  .web{font-weight:800;color:var(--white);text-transform:uppercase;line-height:1}

  /* side panel */
  .side{left:50px;top:110px;width:1100px;height:420px}
  .side .brand-block{right:40px;top:50px;text-align:center}
  .side .brand-name{position:static;font-size:92px}
  .side .brand-sub{position:static;margin-top:8px;font-size:28px;letter-spacing:12px;padding-left:12px}
  .side .phone{right:40px;top:208px;font-size:52px}
  .side .services{left:624px;top:276px;font-size:13px;line-height:17px}
  .side .web{left:121px;top:228px;font-size:17px}

  /* rear panel */
  .rear{left:60px;top:640px;width:480px;height:500px}
  .rear .mark{left:90px;top:84px;width:44px;height:44px;background:var(--red)}
  .rear .brand-name{left:150px;top:70px;font-size:80px}
  .rear .brand-sub{left:185px;top:155px;font-size:24px;letter-spacing:9px}
  .rear .web{left:24px;top:404px;font-size:14px}
  .rear .phone{left:24px;top:426px;font-size:28px}
  .rear .services{left:262px;top:368px;font-size:12px;line-height:19px}

  /* front hood panel */
  .front{left:600px;top:700px;width:540px;height:300px}
  .front .mark{left:152px;top:126px;width:32px;height:32px;background:var(--red)}
  .front .brand-name{left:196px;top:118px;font-size:46px}
  .front .brand-sub{left:218px;top:170px;font-size:14px;letter-spacing:6px}
</style>
</head>
<body>

<section class="panel side" aria-label="Side wrap">
  <svg viewBox="0 0 1100 420" preserveAspectRatio="none">
    <defs>
      <linearGradient id="sideFire" x1="0" y1="1" x2="1" y2="0">
        <stop offset="0" stop-color="var(--red-deep)"/>
        <stop offset=".5" stop-color="var(--red)"/>
        <stop offset=".85" stop-color="var(--orange)"/>
        <stop offset="1" stop-color="var(--yellow)"/>
      </linearGradient>
    </defs>
    <rect width="1100" height="420" fill="var(--white)"/>
    <polygon points="0,0 330,0 545,420 0,420" fill="var(--blue)"/>
    <polygon points="0,300 500,300 545,420 0,420" fill="var(--white)"/>
    <rect x="0" y="290" width="495" height="8" fill="var(--rule)"/>
    <polygon points="365,0 1100,0 1100,420 580,420" fill="url(#sideFire)" role="img" aria-label="Faceted red and orange low-poly colour pattern"/>
    <polygon points="726,0 1100,0 1100,193 658,193" fill="var(--white)"/>
    <rect x="655" y="193" width="445" height="7" fill="var(--rule)"/>
  </svg>
  <div class="abs brand-block">
    <div class="brand-name">ORLA</div>
    <div class="brand-sub">PAINTING</div>
  </div>
  <div class="abs phone">213-555-0148</div>
  <ul class="abs services">
    <li>Interior/Exterior</li>
    <li>Wood Staining</li>
    <li>Cabinet Refinishing</li>
    <li>Drywall Repair.</li>
  </ul>
  <div class="abs web">orlapainting.com</div>
</section>

<section class="panel rear" aria-label="Rear door wrap">
  <svg viewBox="0 0 480 500" preserveAspectRatio="none">
    <defs>
      <linearGradient id="rearFire" x1="0" y1="1" x2="1" y2="0">
        <stop offset="0" stop-color="var(--red-deep)"/>
        <stop offset=".55" stop-color="var(--red)"/>
        <stop offset="1" stop-color="var(--orange)"/>
      </linearGradient>
    </defs>
    <rect width="480" height="500" fill="var(--white)"/>
    <rect x="0" y="300" width="480" height="200" fill="url(#rearFire)" role="img" aria-label="Faceted red and orange low-poly colour pattern"/>
    <rect x="0" y="292" width="480" height="8" fill="var(--rule)"/>
    <rect x="238" y="0" width="3" height="500" fill="var(--rule)" opacity=".5"/>
  </svg>
  <div class="abs mark"></div>
  <div class="abs brand-name">ORLA</div>
  <div class="abs brand-sub">PAINTING</div>
  <div class="abs web">orlapainting.com</div>
  <div class="abs phone">213-555-0148</div>
  <ul class="abs services">
    <li>Interior/Exterior</li>
    <li>Wood Staining</li>
    <li>Cabinet Refinishing</li>
    <li>Drywall Repair.</li>
  </ul>
</section>

<section class="panel front" aria-label="Front hood wrap">
  <svg viewBox="0 0 540 300" preserveAspectRatio="none">
    <rect width="540" height="300" fill="var(--blue)"/>
    <polygon points="100,60 440,60 410,260 130,260" fill="var(--orange)"/>
    <polygon points="112,60 428,60 398,260 142,260" fill="var(--white)"/>
  </svg>
  <div class="abs mark"></div>
  <div class="abs brand-name">ORLA</div>
  <div class="abs brand-sub">PAINTING</div>
</section>

</body>
</html>
```